New Business Card Design

We would like to refresh our business cards and make them look better. We are an IT company specialising in Cloud Services, IT Managed Services, software and hardware. I have attached a PSD of our current design. Also attached our logo.
Updates

I have uploaded all new logos in EPS format.

Can you please edit all designs to include a job title for Marcus Hollis, eg. General Manager

Industry/Entity Type

Software

Colors
ffffff

Requirements
Must have
• Please use white background.
Should not have
• Black background

```html
<!DOCTYPE html>
<html lang="en">
<head>
<meta charset="utf-8">
<title>Meridian Systems – Business Card</title>
<link rel="stylesheet" href="https://fonts.googleapis.com/css2?family=Open+Sans:wght@400;600&display=swap">
<style>
  :root {
    --page-bg: #e9e9ee;
    --card-bg: #ffffff;
    --brand-red: #c0392b;
    --ink-dark: #1f2a30;
    --ink-grey: #55595c;
    --rule: #222222;
    --faint-red: #f6e3e1;
  }
  * { margin: 0; padding: 0; box-sizing: border-box; }
  html, body { width: 1200px; height: 987px; overflow: hidden; }
  body {
    background: var(--page-bg);
    font-family: "Open Sans", Arial, sans-serif;
    position: relative;
  }
  .card {
    position: absolute;
    width: 760px;
    height: 434px;
    background: var(--card-bg);
    border-radius: 34px;
    overflow: hidden;
    box-shadow: 0 10px 30px rgba(0,0,0,0.12);
  }
  /* Back card */
  .card-back { left: 400px; top: 40px; }
  .card-back .faint-circle {
    position: absolute; left: 380px; top: 60px;
    width: 230px; height: 230px; border-radius: 50%;
    background: var(--faint-red);
  }
  .card-back .company-name {
    position: absolute; left: 110px; top: 120px;
    font-size: 60px; font-weight: 400; letter-spacing: 6px;
    color: var(--ink-dark);
  }
  .card-back .tagline {
    position: absolute; left: 110px; top: 250px;
    font-size: 24px; line-height: 1.35; color: var(--ink-grey);
  }
  /* Front card */
  .card-front { left: 60px; top: 500px; }
  .brand {
    position: absolute; left: 50px; top: 40px;
    display: flex; align-items: center; gap: 16px;
  }
  .brand .mark {
    width: 54px; height: 54px; border-radius: 50%;
    background: var(--brand-red);
  }
  .brand .company-name {
    font-size: 40px; font-weight: 400; letter-spacing: 4px;
    color: var(--ink-dark);
  }
  .holder {
    position: absolute; left: 50px; top: 140px;
    font-size: 22px; color: var(--ink-dark);
  }
  .holder .name { color: var(--brand-red); font-weight: 600; }
  .contacts {
    position: absolute; left: 50px; top: 184px;
    list-style: none; font-size: 18px; color: var(--ink-grey);
  }
  .contacts li { display: flex; align-items: center; gap: 12px; height: 32px; }
  .contacts svg { width: 18px; height: 18px; fill: var(--brand-red); }
  .rule {
    position: absolute; left: 0; right: 0; top: 322px;
    height: 2px; background: var(--rule);
  }
  .band {
    position: absolute; left: 0; right: 0; top: 330px; bottom: 0;
    background: var(--brand-red);
    display: flex; align-items: center; padding-left: 50px;
  }
  .band .web { color: #ffffff; font-size: 24px; letter-spacing: 1px; }
</style>
</head>
<body>

<section class="card card-back" aria-label="Card back">
  <div class="faint-circle"></div>
  <div class="company-name">Meridian Systems</div>
  <p class="tagline">We are an IT company specializing in Cloud Services<br>IT Managed Services, software and hardware</p>
</section>

<section class="card card-front" aria-label="Card front">
  <div class="brand">
    <div class="mark"></div>
    <div class="company-name">Meridian Systems</div>
  </div>
  <p class="holder"><span class="name">Marcus Hollis,</span> General Manager</p>
  <ul class="contacts">
    <li>
      <svg viewBox="0 0 24 24" aria-hidden="true"><path d="M6.6 10.8a15.1 15.1 0 0 0 6.6 6.6l2.2-2.2a1 1 0 0 1 1-.25 11.4 11.4 0 0 0 3.6.57 1 1 0 0 1 1 1V20a1 1 0 0 1-1 1A17 17 0 0 1 3 4a1 1 0 0 1 1-1h3.5a1 1 0 0 1 1 1c0 1.25.2 2.45.57 3.57a1 1 0 0 1-.25 1z"/></svg>
      07 5550 1234
    </li>
    <li>
      <svg viewBox="0 0 24 24" aria-hidden="true"><path d="M7 1h10a2 2 0 0 1 2 2v18a2 2 0 0 1-2 2H7a2 2 0 0 1-2-2V3a2 2 0 0 1 2-2zm0 3v14h10V4zm5 15.5a1.2 1.2 0 1 0 0 2.4 1.2 1.2 0 0 0 0-2.4z"/></svg>
      0400 555 017
    </li>
    <li>
      <svg viewBox="0 0 24 24" aria-hidden="true"><path d="M2 5h20v14H2zm2 2v.5l8 5 8-5V7zm0 2.8V17h16V9.8l-8 5z"/></svg>
      mhollis@meridiansys.com.au
    </li>
  </ul>
  <div class="rule"></div>
  <div class="band"><span class="web">www.meridiansys.com.au</span></div>
</section>

</body>
</html>
```